Mastering Modern Vineyard Management

size of the ad - 8”x 10.75" plus 0.25" bleed
I would like an ad for a magazine that will stand out and make people want to read the ad.
The ad should not be crowded and people reading the ad will be able to read the text.
I would like it to be a creative and modern-day design.
the list of topics should not be the focus of the ad.
the text is attached.
If you decide to use people in the ad then please no ladies.
please note that leave over 1 inch for the bottom of the footer

```html
<!DOCTYPE html>
<html lang="en">
<head>
<meta charset="utf-8">
<title>Mastering Modern Vineyard Management – Course Ad</title>
<link rel="stylesheet" href="https://fonts.googleapis.com/css2?family=Oswald:wght@300;600&family=Montserrat:wght@400&display=swap">
<style>
  :root {
    --backdrop: #e4e4e4;
    --page: #231f20;
    --ink: #ffffff;
    --accent: #d6262b;
    --muted: #bdbdbd;
    --sky-top: #6f9fc4;
    --sky-low: #b9d3e4;
    --lawn: #6f7a44;
  }
  * { margin: 0; padding: 0; box-sizing: border-box; }
  html, body { width: 1200px; height: 873px; overflow: hidden; background: var(--backdrop); }
  .canvas { position: relative; width: 1200px; height: 873px; display: flex; align-items: center; justify-content: center; }
  .ad-page {
    position: relative; width: 624px; height: 826px; background: var(--page);
    box-shadow: 0 8px 30px rgba(0,0,0,.18); overflow: hidden;
  }
  .masthead {
    position: absolute; left: 44px; top: 46px; width: 460px; color: var(--ink);
    font-family: "Oswald", sans-serif; font-weight: 300; font-size: 30px;
    letter-spacing: .5px; line-height: 1.08; text-transform: uppercase;
  }
  .masthead-marker { position: absolute; right: 64px; top: 58px; width: 26px; height: 26px; background: var(--accent); }
  .hero-photo {
    position: absolute; left: 40px; top: 138px; width: 520px; height: 420px;
    background: linear-gradient(180deg, var(--sky-top) 0%, var(--sky-low) 45%, #e9ecee 62%, var(--lawn) 88%);
  }
  .hero-dates {
    position: absolute; left: 58px; top: 392px; font-family: "Oswald", sans-serif; font-weight: 600;
    text-transform: uppercase; font-size: 31px; line-height: 1.02; color: var(--ink);
    text-shadow: 0 2px 4px rgba(0,0,0,.55);
  }
  .hero-dates .highlight { color: var(--accent); }
  .scholarship-note {
    position: absolute; right: 40px; top: 560px; writing-mode: vertical-rl; transform: rotate(180deg);
    font-family: "Oswald", sans-serif; font-weight: 300; font-size: 13px; letter-spacing: 1.5px;
    color: var(--ink); white-space: nowrap;
  }
  .offer { position: absolute; left: 58px; top: 600px; right: 80px; color: var(--ink); }
  .offer-lead { font-family: "Oswald", sans-serif; font-weight: 300; font-size: 19px; letter-spacing: 1.2px; line-height: 1.3; text-transform: uppercase; }
  .topic-list { margin-top: 22px; font-family: "Montserrat", sans-serif; font-size: 10px; letter-spacing: .8px; line-height: 1.7; color: var(--muted); }
</style>
</head>
<body>
<main class="canvas">
  <article class="ad-page">
    <h1 class="masthead">Mastering Modern Vineyard Management Course</h1>
    <span class="masthead-marker" aria-hidden="true"></span>
    <div class="hero-photo" role="img" aria-label="Photo of a modern white house with a lawn and a pine tree under a blue sky"></div>
    <p class="hero-dates">Starting Feb 28<br><span class="highlight">Monday 10 AM – Tuesday</span><br>Evenings Sessions</p>
    <p class="scholarship-note">LIMITED PARTIAL SCHOLARSHIPS</p>
    <section class="offer">
      <p class="offer-lead">Early bird special for those that<br>started or would like to go into real estate</p>
      <p class="topic-list">Partial listing &nbsp;|&nbsp; Real estate investment strategies &nbsp;|&nbsp; Due diligence<br>Financing &nbsp;|&nbsp; Underwriting &nbsp;|&nbsp; Property management &nbsp;|&nbsp; Real estate Legal basics<br>Sourcing deals &nbsp;|&nbsp; Syndication &nbsp;|&nbsp; Dealing with brokers &nbsp;|&nbsp; Tax fundamentals</p>
    </section>
  </article>
</main>
</body>
</html>
```